Website Design for The Elder Nook

Please design and code a new website.
Here are the sites I like best:
http://www.voyaglint.com/alternate/
http://www.wheelgiftbay.org
Please make it similar but look at the competitor site (below) for images and wording. This is NOT a car donation site. It's a senior lead placement site like https://www.kinhavenfinder.com. I just like this sites above as a lead generation sites.
Competitor site:
https://www.kinhavenfinder.com (use ideas / verbiage from this site)
Updates
Competitor site:
Coding
Coded - Design and coding required
Number of Pages Required
1 page
Look and feel
Each slider illustrates characteristics of the customer's brand and the style your logo design should communicate.

```html
<!DOCTYPE html>
<html lang="en">
<head>
<meta charset="utf-8">
<title>The Elder Nook</title>
<link href="https://fonts.googleapis.com/css2?family=Poppins:wght@300;400;500&family=Open+Sans:wght@400;600&display=swap" rel="stylesheet">
<style>
:root{
  --navy:#0b4587;
  --navy-dark:#073870;
  --gold:#f6a91c;
  --band:#e4a233;
  --page:#e4e4e4;
  --panel:#f0f0f0;
  --ink:#333;
  --muted:#555;
  --white:#fff;
}
*{margin:0;padding:0;box-sizing:border-box}
html,body{width:1200px;height:2304px;overflow:hidden}
body{background:var(--page);font-family:"Open Sans",sans-serif;color:var(--ink)}
.site{position:absolute;left:157px;top:0;width:885px;height:2304px;background:var(--white)}
.abs{position:absolute}

.header{height:76px;position:relative}
.brand{position:absolute;left:15px;top:12px;font-family:"Poppins",sans-serif;font-weight:500;font-size:37px;color:var(--navy);letter-spacing:-.5px}
.phone{position:absolute;right:15px;top:24px;font-family:"Poppins",sans-serif;font-weight:300;font-size:18px;color:#666;display:flex;align-items:center;gap:6px}

.nav{position:absolute;top:76px;left:0;width:885px;height:37px;background:var(--navy);display:flex;font-family:"Poppins",sans-serif;font-size:12.3px;color:#c9d6e8}
.nav a{display:flex;align-items:center;justify-content:center;text-decoration:none;color:inherit;height:100%}
.nav a.active{background:var(--navy-dark);color:var(--white)}

.hero{position:absolute;top:113px;left:0;width:885px;height:463px}
.hero-photo{position:absolute;inset:0;background:linear-gradient(110deg,#b9b6b2 0%,#8c8781 30%,#5b5650 50%,#9b968f 70%,#d2cfca 100%)}
.hero-copy{position:absolute;right:45px;top:45px;text-align:right;font-family:"Poppins",sans-serif}
.hero-copy h1{font-size:24px;font-weight:500;color:var(--navy);line-height:34px}
.hero-copy p{font-size:14.5px;color:#222;margin-top:5px}
.search-input{position:absolute;left:585px;top:145px;width:254px;height:35px;background:var(--white);border:1px solid #ddd;font-size:12px;padding:0 17px;display:flex;align-items:center;color:#333}
.search-btn{position:absolute;left:585px;top:189px;width:254px;height:37px;background:var(--gold);font-family:"Poppins",sans-serif;font-size:14.5px;color:#1a1a1a;display:flex;align-items:center;justify-content:center}
.arrow{position:absolute;top:218px;width:23px;height:29px;background:rgba(30,30,30,.75);display:flex;align-items:center;justify-content:center}

.support{position:absolute;top:640px;left:0;width:885px;text-align:center}
.support h2{font-family:"Poppins",sans-serif;font-weight:300;font-size:26px;color:var(--navy)}
.support p{font-size:11.5px;color:#444;line-height:19.5px;margin:14px 20px 0}
.features{position:absolute;top:769px;left:0;width:885px;display:flex;justify-content:space-between;padding:0 0}
.feature{width:177px;text-align:center;font-size:11.5px;color:var(--navy);line-height:16.5px}
.feature svg{display:block;margin:0 auto 8px;height:40px}

.reviews{position:absolute;top:923px;left:0;width:885px;height:464px;background:linear-gradient(90deg,#e7a536,#dd9b2c 50%,#e6a43a)}
.reviews h2{position:absolute;top:46px;width:100%;text-align:center;font-family:"Poppins",sans-serif;font-weight:400;font-size:26px;color:var(--white)}
.card{position:absolute;top:95px;width:274px;height:280px;background:var(--white);text-align:center;padding:20px 18px 0}
.card blockquote{font-family:"Poppins",sans-serif;font-weight:300;font-size:12.3px;line-height:22.4px;color:#333;height:145px}
.avatar{width:74px;height:74px;border-radius:50%;margin:0 auto;background:radial-gradient(circle at 50% 40%,#e8d9cc,#c9b8aa 60%,#eee 62%)}
.card .name{font-family:"Poppins",sans-serif;font-size:14px;color:var(--navy);margin-top:7px}
.card .role{font-size:9.5px;color:#666;margin-top:1px}
.dots{position:absolute;top:398px;left:0;width:100%;display:flex;justify-content:center;gap:11px}
.dots span{width:11px;height:11px;border-radius:50%;background:#6b4a14}
.dots span.on{background:var(--white)}

.care{position:absolute;top:1463px;width:274px}
.care .photo{height:179px}
.care .label{height:38px;background:var(--navy);color:var(--white);font-family:"Roboto","Open Sans",sans-serif;font-size:14.5px;display:flex;align-items:center;justify-content:center;letter-spacing:.2px}

.faq-title{position:absolute;top:1722px;width:100%;text-align:center;font-family:"Poppins",sans-serif;font-weight:300;font-size:26px;color:var(--navy)}
.faq{position:absolute;left:15px;width:856px;background:var(--panel);font-family:"Poppins",sans-serif}
.faq .q{position:absolute;left:52px;font-size:17.5px;font-weight:300;color:#555}
.faq.open .q{color:var(--navy);font-weight:400}
.faq .toggle{position:absolute;left:22px;width:13px;height:13px;border-radius:2px;background:#666}
.faq.open .toggle{background:var(--navy)}
.faq .toggle::before,.faq .toggle::after{content:"";position:absolute;background:var(--white);left:3px;top:6px;width:7px;height:1.6px}
.faq .toggle::after{left:5.7px;top:3px;width:1.6px;height:7px}
.faq.open .toggle::after{display:none}
.faq .a{position:absolute;left:53px;top:48px;width:780px;font-family:"Open Sans",sans-serif;font-size:10.7px;line-height:18px;color:#444}

.footer{position:absolute;top:2213px;left:0;width:885px;height:91px;background:var(--navy);color:#d8e2ef}
.footer .links{position:absolute;left:16px;top:30px;font-size:9.8px}
.footer .links span{margin:0 7px}
.footer .copy{position:absolute;left:16px;top:57px;font-size:9.8px}
.social{position:absolute;right:20px;top:33px;display:flex;gap:14px}
.social span{width:16px;height:16px;border-radius:50%;background:#b9cbe2}
</style>
</head>
<body>
<div class="site">
  <header class="header">
    <div class="brand">The Elder Nook</div>
    <div class="phone">
      <svg width="14" height="14" viewBox="0 0 24 24"><path fill="#777" d="M6.6 10.8a15.1 15.1 0 0 0 6.6 6.6l2.2-2.2c.3-.3.7-.4 1-.2 1.1.4 2.3.6 3.6.6.6 0 1 .4 1 1V20c0 .6-.4 1-1 1A17 17 0 0 1 3 4c0-.6.4-1 1-1h3.5c.6 0 1 .4 1 1 0 1.3.2 2.5.6 3.6.1.3 0 .7-.2 1z"/></svg>
      555 014 2290
    </div>
  </header>

  <nav class="nav">
    <a class="active" style="width:131px">Assisted Living</a>
    <a style="width:126px">Memory Care</a>
    <a style="width:134px">Nursing Homes</a>
    <a style="width:158px">More Living Options&nbsp;<svg width="8" height="6" viewBox="0 0 8 6"><path fill="#c9d6e8" d="M0 0h8L4 5z"/></svg></a>
    <a style="width:149px">Planning &amp; Advice</a>
    <a style="width:187px">How Our Service Works</a>
  </nav>

  <section class="hero">
    <div class="hero-photo" role="img" aria-label="Caregiver kneeling beside a smiling senior man in a wheelchair in a bright room"></div>
    <div class="hero-copy">
      <h1>You know your family.<br>We know Senior Living.</h1>
      <p>Find Senior Living Near You.</p>
    </div>
    <div class="search-input">Enter city or postal code</div>
    <div class="search-btn">START YOUR SEARCH</div>
    <div class="arrow" style="left:0"><svg width="10" height="18" viewBox="0 0 10 18"><path d="M9 1 1 9l8 8" fill="none" stroke="#fff" stroke-width="1.3"/></svg></div>
    <div class="arrow" style="right:0"><svg width="10" height="18" viewBox="0 0 10 18"><path d="m1 1 8 8-8 8" fill="none" stroke="#fff" stroke-width="1.3"/></svg></div>
  </section>

  <section class="support">
    <h2>The support you need to make the right choice</h2>
    <p>Etiam sit amet velit ut nibh ullamcorper rhoncus vel vitae risus. In condimentum purus libero, non pellentesque dui blandit quis. Duis rutrum venenatis tristique. Nam vitae placerat dui, nec sagittis sem. Aliquam a lacus in enim viverra congue. Aliquam interdum tortor erat, eget porta elit molestie et. Aenean tortor magna, iaculis vitae condimentum vitae, laoreet eget erat. Praesent sollicitudin, justo quis faucibus dapibus.</p>
  </section>
  <div class="features">
    <div class="feature"><svg viewBox="0 0 40 40" width="40"><circle cx="20" cy="12" r="9" fill="#0b4587"/><path d="M3 39c0-10 7-15 17-15s17 5 17 15z" fill="#0b4587"/></svg>Quisque venenatis viverra<br>leo eu vulputate</div>
    <div class="feature"><svg viewBox="0 0 44 40" width="44"><path d="M22 4 2 21h5v16h11V27h8v10h11V21h5z" fill="#0b4587"/><rect x="31" y="5" width="5" height="10" fill="#0b4587"/></svg>Fusce aliquet efficitur<br>auctor</div>
    <div class="feature"><svg viewBox="0 0 36 40" width="36"><rect x="1" y="6" width="34" height="33" rx="3" fill="#0b4587"/><rect x="8" y="1" width="4" height="9" rx="1" fill="#0b4587"/><rect x="24" y="1" width="4" height="9" rx="1" fill="#0b4587"/><g fill="#fff"><rect x="6" y="16" width="6" height="5"/><rect x="15" y="16" width="6" height="5"/><rect x="24" y="16" width="6" height="5"/><rect x="6" y="25" width="6" height="5"/><rect x="15" y="25" width="6" height="5"/><rect x="24" y="25" width="6" height="5"/></g></svg>Aenean mattis volutpat<br>massa</div>
    <div class="feature"><svg viewBox="0 0 40 40" width="40"><path d="M6 3v12a10 10 0 0 0 20 0V3" fill="none" stroke="#0b4587" stroke-width="4"/><path d="M16 25v4a8 8 0 0 0 16 0v-7" fill="none" stroke="#0b4587" stroke-width="4"/><circle cx="32" cy="17" r="5" fill="#0b4587"/><circle cx="32" cy="17" r="2" fill="#fff"/></svg>Vivamus hendrerit<br>maximus tempus</div>
    <div class="feature"><svg viewBox="0 0 48 40" width="48"><rect x="1" y="8" width="46" height="26" fill="#0b4587"/><circle cx="24" cy="21" r="8" fill="#fff"/><path d="M23 17h2v8h-2z" fill="#0b4587"/><g fill="#fff"><path d="M4 11h5l-5 5z"/><path d="M44 11h-5l5 5z"/><path d="M4 31h5l-5-5z"/><path d="M44 31h-5l5-5z"/></g></svg>Proin efficitur sem nec<br>imperdiet</div>
  </div>

  <section class="reviews" role="img" aria-label="Warm amber-tinted band showing a caregiver and senior together">
    <h2>97% of our customers recommend our service</h2>
    <div class="card" style="left:15px">
      <blockquote>“ Suspendisse volutpat ligula turpis. In elementum purus sed ante ultricies, ac aliquam ante dignissim. In hac habi-tasse platea dictumst. In id euismod lorem. Nulla diam purus. ”</blockquote>
      <div class="avatar" role="img" aria-label="Portrait of a smiling senior man with glasses"></div>
      <div class="name">Walter Hale</div><div class="role">Vestibulum ultrices amet</div>
    </div>
    <div class="card" style="left:305px">
      <blockquote>“ Duis rutrum venenatis tristique. Nam vitae placerat dui, nec sagittis sem. Aliquam a lacus in enim viverra congue. Aliquam interdum tortor erat, eget porta elit molestie et. ”</blockquote>
      <div class="avatar" role="img" aria-label="Portrait of a smiling grey-haired man"></div>
      <div class="name">Arthur</div><div class="role">Vestibulum ultrices amet</div>
    </div>
    <div class="card" style="left:595px">
      <blockquote>“ Maecenas mattis sem urna, sed pharetra enim pretium a. Suspendisse volutpat ligula turpis. In elementum purus sed ante ultricies, ac aliquam ante dignissim. ”</blockquote>
      <div class="avatar" role="img" aria-label="Portrait of a smiling senior man"></div>
      <div class="name">Edwin</div><div class="role">Vestibulum ultrices amet</div>
    </div>
    <div class="dots"><span class="on"></span><span></span><span></span><span></span></div>
  </section>

  <div class="care" style="left:15px">
    <div class="photo" role="img" aria-label="Cheerful senior man in a plaid shirt at home" style="background:linear-gradient(160deg,#d9d4cc,#9e8f84 55%,#6f6a78)"></div>
    <div class="label">INDEPENDENT LIVING</div>
  </div>
  <div class="care" style="left:305px">
    <div class="photo" role="img" aria-label="Senior man with a cane sitting beside a smiling young woman" style="background:linear-gradient(160deg,#c8d2b8,#a79a8a 50%,#b9c7d2)"></div>
    <div class="label">MEMORY CARE</div>
  </div>
  <div class="care" style="left:595px">
    <div class="photo" role="img" aria-label="Nurse in blue scrubs helping a senior man from a bed" style="background:linear-gradient(160deg,#d6dbc8,#b1aba0 45%,#6f9fc9)"></div>
    <div class="label">NURSING HOMES</div>
  </div>

  <h2 class="faq-title">Frequently Asked Questions</h2>
  <div class="faq open" style="top:1782px;height:122px">
    <span class="toggle" style="top:23px"></span>
    <div class="q" style="top:15px">Maecenas sed nibh sed nisi tristique pharetra?</div>
    <p class="a">Nullam varius, orci nec porttitor cursus, eros diam viverra sapien, a convallis mauris augue eget erat. Sed efficitur lorem vel est rhoncus rutrum. Suspendisse porttitor auctor vehicula. In sodales sem a lectus viverra, vitae varius nisi sodales. Aliquam cursus dolor vel interdum pellentesque. Fusce convallis venenatis pulvinar. Curabitur vel dapibus tellus. Vivamus dolor sapien, sollicitudin nec pulvinar sit amet, vulputate at elit.</p>
  </div>
  <div class="faq" style="top:1909px;height:60px"><span class="toggle" style="top:24px"></span><div class="q" style="top:16px">Donec aliquam quam eget euismod dictum?</div></div>
  <div class="faq" style="top:1972px;height:60px"><span class="toggle" style="top:24px"></span><div class="q" style="top:16px">Aliquam dignissim elit nec mauris porta?</div></div>
  <div class="faq" style="top:2036px;height:60px"><span class="toggle" style="top:24px"></span><div class="q" style="top:16px">Nulla porttitor nibh ut mi feugiat rhoncus quis in ante?</div></div>
  <div class="faq" style="top:2100px;height:60px"><span class="toggle" style="top:24px"></span><div class="q" style="top:16px">Nam tempus augue eu ante lacinia euismod sodales ligula porttitor?</div></div>

  <footer class="footer">
    <div class="links">Assisted Living<span>|</span>Memory Care<span>|</span>Nursing Homes<span>|</span>More Living Options<span>|</span>Planning &amp; Advice<span>|</span>How Our Service Works</div>
    <div class="copy">Copyright © 2019 &nbsp;The Elder Nook. &nbsp;All rights reserved.</div>
    <div class="social"><span></span><span></span></div>
  </footer>
</div>
</body>
</html>
```